CREATE A BUSINESS CARD FOR A BOAT CLEANING SERVICE

WE ARE STARTING A NEW BOAT CLEANING BUSINESS. WE DIVE UNDERWATER TO CLEAN BOAT HULLS, JETTIES, UNDERWATER STRUCTURES ETC. WE ARE LOOKING FOR AN UPPERMARKET MODERN LOGO AND BUSINESS CARD AS ALOT OF OUR TARGET MARKET WILL BE HIGH END. YOU HAVE TO DESIGN A BUSINESS CARD AND LOGO SEPERATELY .
THE BUSINESS CARD DIMESNION MUST BE STANDARD SIZE.
The standard dimensions of a printed business card are 3.5 x 2 inches

Target Market(s)

UNDERWATER SERVICED

Industry/Entity Type

Business

Contact Information for Business Card

HOLLAND UNDERWATER SERVICES

Font styles to use
Serif

Colors

Designer to choose colors to be used in the design.

Requirements
Must have
• HOLLAND
Nice to have
• dark
Should not have
• more than 3 colors

```html
<!DOCTYPE html>
<html lang="en">
<head>
<meta charset="utf-8">
<title>Holland Underwater Service – Business Card</title>
<link rel="stylesheet" href="https://fonts.googleapis.com/css2?family=Raleway:wght@300;400;500;600&display=swap">
<style>
  :root {
    --page: #e9ebee;
    --card: #ffffff;
    --blue: #1d6fb3;
    --blue-deep: #14588f;
    --blue-light: #4a9ccf;
    --grey: #c9cbce;
    --grey-light: #e2e3e5;
    --text-soft: #a9abae;
    --shadow: rgba(20, 40, 60, 0.18);
  }
  html, body {
    margin: 0;
    width: 1200px;
    height: 1023px;
    overflow: hidden;
    background: var(--page);
    font-family: "Raleway", sans-serif;
  }
  .sheet {
    position: relative;
    width: 1200px;
    height: 1023px;
  }
  .card {
    position: absolute;
    left: 250px;
    width: 700px;
    height: 400px;
    border-radius: 18px;
    overflow: hidden;
    background: var(--card);
    box-shadow: 0 10px 30px var(--shadow);
  }
  .card--front { top: 60px; }
  .card--back { top: 563px; }
  .card svg.shapes {
    position: absolute;
    inset: 0;
  }
  .contact {
    position: absolute;
    left: 48px;
    top: 178px;
    color: var(--text-soft);
    font-size: 17px;
    font-weight: 300;
    line-height: 1.5;
  }
  .contact__name {
    margin: 0;
    color: var(--blue);
    font-size: 32px;
    font-weight: 500;
    letter-spacing: 0.5px;
    line-height: 1.1;
  }
  .contact__role {
    margin: 2px 0 14px;
    font-size: 17px;
  }
  .contact p { margin: 0; }
  .contact__line {
    display: flex;
    align-items: center;
    gap: 10px;
  }
  .contact__line svg { flex: none; }
  .wordmark {
    position: absolute;
    text-align: left;
  }
  .wordmark__name {
    display: block;
    color: var(--blue);
    font-size: 30px;
    font-weight: 400;
    letter-spacing: 16px;
  }
  .wordmark__tag {
    display: block;
    margin-top: 4px;
    color: var(--text-soft);
    font-size: 14px;
    font-weight: 400;
    letter-spacing: 5px;
  }
  .wordmark__square {
    position: absolute;
    left: -46px;
    top: 6px;
    width: 30px;
    height: 30px;
    background: var(--blue);
  }
  .card--front .wordmark { left: 120px; top: 58px; }
  .card--back .wordmark { left: 300px; top: 170px; }
  .band-mark {
    position: absolute;
    right: 26px;
    bottom: 54px;
    display: flex;
    align-items: center;
    gap: 12px;
    color: var(--card);
    font-size: 26px;
    font-weight: 600;
    letter-spacing: 1px;
  }
  .band-mark__dot {
    width: 30px;
    height: 30px;
    border-radius: 50%;
    background: var(--card);
  }
  .band-badge {
    position: absolute;
    right: 190px;
    bottom: 22px;
    width: 36px;
    height: 36px;
    border-radius: 50%;
    background: var(--blue-light);
    border: 2px solid var(--card);
  }
</style>
</head>
<body>
<main class="sheet">

  <section class="card card--front" aria-label="Business card front">
    <svg class="shapes" width="700" height="400" viewBox="0 0 700 400" aria-hidden="true">
      <polygon points="470,0 610,0 700,180 700,400 520,400" fill="var(--grey-light)"/>
      <polygon points="470,0 600,0 560,400 520,400" fill="var(--grey)"/>
      <polygon points="612,0 700,0 700,170" fill="var(--blue)" stroke="#fff" stroke-width="4"/>
      <polygon points="556,262 700,232 700,400 530,400" fill="var(--blue)" stroke="#fff" stroke-width="4"/>
      <polygon points="530,400 556,262 600,253 580,400" fill="var(--blue-light)" opacity="0.55"/>
    </svg>

    <div class="wordmark">
      <span class="wordmark__square"></span>
      <span class="wordmark__name">HOLLAND</span>
      <span class="wordmark__tag">UNDERWATER SERVICE</span>
    </div>

    <div class="contact">
      <h1 class="contact__name">DARREN HALE</h1>
      <p class="contact__role">President</p>
      <p>140, 318- 9th Ave, SW</p>
      <p>Calgary, AB T2P 1K4</p>
      <p class="contact__line">
        <svg width="12" height="12" viewBox="0 0 12 12"><path d="M2 1h3l1 3-2 1a7 7 0 0 0 3 3l1-2 3 1v3c0 1-1 1-1 1A10 10 0 0 1 1 2s0-1 1-1z" fill="var(--blue)"/></svg>
        (410) 555-0192
      </p>
      <p class="contact__line">
        <svg width="12" height="12" viewBox="0 0 12 12"><rect x="0.5" y="2" width="11" height="8" fill="none" stroke="var(--blue)"/><path d="M1 2.5l5 4 5-4" fill="none" stroke="var(--blue)"/></svg>
        info@hollandunderwater.com
      </p>
      <p class="contact__line">
        <svg width="12" height="12" viewBox="0 0 12 12"><circle cx="6" cy="6" r="5.5" fill="var(--blue)"/><path d="M0.5 6h11M6 0.5v11" stroke="#fff" stroke-width="0.8"/></svg>
        www.hollandunderwater.com
      </p>
    </div>

    <span class="band-badge" aria-hidden="true"></span>
    <div class="band-mark"><span class="band-mark__dot"></span>HOLLAND</div>
  </section>

  <section class="card card--back" aria-label="Business card back">
    <svg class="shapes" width="700" height="400" viewBox="0 0 700 400" aria-hidden="true">
      <polygon points="0,0 150,0 0,230" fill="var(--blue)" stroke="#fff" stroke-width="4"/>
      <polygon points="150,0 260,0 130,400 0,400 0,230" fill="var(--grey-light)"/>
      <polygon points="150,0 230,0 60,400 0,400 0,250" fill="var(--grey)"/>
      <polygon points="0,300 0,400 250,400 420,320" fill="var(--blue-deep)" stroke="#fff" stroke-width="4"/>
      <polygon points="610,0 700,0 700,110" fill="var(--blue)" stroke="#fff" stroke-width="4"/>
    </svg>

    <div class="wordmark">
      <span class="wordmark__square"></span>
      <span class="wordmark__name">HOLLAND</span>
      <span class="wordmark__tag">UNDERWATER SERVICE</span>
    </div>
  </section>

</main>
</body>
</html>
```